Double sided packaging design

Using our logo and its colors, please design a packaging design for our new Product Vontrisa.
The printable size is 140mm x 180mm, both sides
Vontrisa is a powdered formula of Cinnamon, turmeric, fennel, black pepper, 4 types of kelp & Seaweed, stevia and vanilla.
Its the flavor sensation that energizes your bodies Cells giving them all the food it needs to be healthy.

The old packaging we are moving away from as we have a new formula and we are also marketing for USA
It helps people with pain relief as its proven scientifically to reduce inflammation and other health benefits within the body such as cellular growth.

Please keep to the new colors of the Vontrisa Logo as supplied below

Target Market(s)

older women

Industry/Entity Type

Health Suplement Turmeric

Colors
59FF00
82FF00
B8FF75
E3FFCB
F4FFEA
FFC000
F8CF3A
FAE287
FDF2CF
FEFAEE

Requirements
Should not have
• not be too busy

```html
<!DOCTYPE html>
<html lang="en">
<head>
<meta charset="utf-8">
<title>Vontrisa Turmeric Thai Tea – Pouch Front and Back</title>
<link rel="stylesheet" href="https://fonts.googleapis.com/css2?family=Cormorant+Garamond:wght@500;600&family=Old+Standard+TT&family=Oswald:wght@200;400;500;600&family=Roboto+Condensed:wght@300;400;700&display=swap">
<style>
  :root {
    --green-deep: #1f8a3e;
    --green: #2fa24a;
    --green-bright: #6cc04a;
    --lime: #b8e063;
    --gold: #e4b228;
    --gold-soft: #f8cf3a;
    --gold-pale: #fae287;
    --cream: #fdf2cf;
    --white: #ffffff;
    --ink: #1c1c1c;
    --grey: #4a4a4a;
    --bg: #f2f2f2;
  }
  * { box-sizing: border-box; margin: 0; padding: 0; }
  html, body { width: 1200px; height: 860px; overflow: hidden; background: var(--bg); }
  body { position: relative; font-family: "Roboto Condensed", sans-serif; }

  .pouch { position: absolute; top: 60px; width: 500px; height: 740px; border-radius: 18px; overflow: hidden; box-shadow: 0 10px 30px rgba(0,0,0,.15); }
  .pouch--front { left: 60px; background: linear-gradient(170deg, var(--green-bright), var(--green) 55%, var(--green-deep)); }
  .pouch--back { left: 640px; background: linear-gradient(180deg, #fafafa, #e9e9e9); }

  .leaf-band { position: absolute; left: 0; top: 0; width: 100%; height: 92px; background: linear-gradient(90deg, var(--green-deep), var(--green-bright) 50%, var(--green)); }
  .pouch--back .leaf-band { height: 110px; }

  .abs { position: absolute; }

  /* front hero */
  .hero-frame { left: 0; top: 92px; width: 500px; height: 312px; background: var(--gold); }
  .hero { left: 22px; top: 16px; width: 456px; height: 280px; overflow: hidden; background: var(--cream); }
  .hero-photo { left: 200px; top: 0; width: 256px; height: 280px; background: linear-gradient(160deg, #e9cf8f, #c9a45a 60%, #b8b07a); }
  .hero-curve { left: 0; top: 0; }
  .brand-art { width: 170px; height: 80px; border-radius: 50% 50% 40% 40%; background: radial-gradient(circle at 45% 50%, #4a3a2c 0 18%, #5fae4a 19%, #9fd06a 55%, rgba(159,208,106,0) 72%); }
  .brand-name { font-family: "Cormorant Garamond", serif; font-weight: 500; color: var(--gold); letter-spacing: 1px; line-height: 1; white-space: nowrap; }
  .kicker { font-family: "Old Standard TT", serif; font-size: 10px; letter-spacing: 2px; color: var(--ink); white-space: nowrap; }
  .kicker span { color: var(--gold); }
  .tagline { font-size: 10.5px; line-height: 13px; color: #d8962a; font-weight: 300; }
  .title-serif { font-family: "Old Standard TT", serif; color: var(--ink); font-size: 28px; line-height: 29px; }
  .title-tea { font-family: "Oswald", sans-serif; font-weight: 200; font-size: 112px; line-height: 100px; color: var(--ink); letter-spacing: -2px; }
  .title-sub { font-family: "Oswald", sans-serif; font-weight: 500; font-size: 15px; color: var(--ink); letter-spacing: .5px; white-space: nowrap; }
  .seam { left: 0; top: 404px; width: 500px; border-top: 1.5px dashed rgba(255,255,255,.7); }

  .ingredient { width: 64px; height: 64px; border-radius: 50%; border: 4px solid var(--white); box-shadow: 0 0 0 2px rgba(255,255,255,.35); }
  .ing-turmeric { background: radial-gradient(circle, #f2a43a, #c86a1e); }
  .ing-cinnamon { background: radial-gradient(circle, #c8874a, #7a4622); }
  .ing-pepper { background: radial-gradient(circle, #4b3a30, #1e1814); }
  .ing-fennel { background: radial-gradient(circle, #b8a47a, #6f6448); }
  .ing-kelp { background: radial-gradient(circle, #6ea27a, #2f6a6a); }
  .ing-seaweed { background: radial-gradient(circle, #5f9a5a, #2e5a34); }
  .ing-stevia { background: radial-gradient(circle, #7fb85a, #8a8a8a); }
  .ing-vanilla { background: radial-gradient(circle, #f6e6a0, #6b4a2a); }

  .claim-box { left: 28px; top: 576px; width: 168px; height: 150px; background: linear-gradient(135deg, #c9cf6a, #8fa83a 60%, #5c8a2e); }
  .claim-frame { left: 12px; top: 10px; width: 136px; height: 130px; border: 2px solid var(--white); }
  .claim { font-family: "Oswald", sans-serif; font-weight: 600; color: var(--ink); line-height: .95; text-transform: uppercase; }

  .origin-mark { left: 232px; top: 612px; width: 40px; height: 40px; border-radius: 50%; background: #e8e0d0; }
  .origin { left: 206px; top: 662px; font-family: "Oswald", sans-serif; font-weight: 200; color: var(--gold-soft); font-size: 15px; letter-spacing: 2.5px; line-height: 1; white-space: nowrap; }
  .origin small { display: block; font-size: 7px; letter-spacing: 2.5px; color: var(--cream); margin-top: 3px; }

  .mini-block { left: 316px; top: 530px; width: 176px; }
  .mini-sub { font-family: "Old Standard TT", serif; font-size: 12px; color: var(--white); white-space: nowrap; }
  .mini-sub span { color: var(--gold-soft); }
  .mini-list { font-family: "Oswald", sans-serif; font-size: 7.5px; line-height: 11px; color: var(--white); text-transform: uppercase; white-space: nowrap; }
  .method { font-family: "Oswald", sans-serif; color: var(--gold-soft); text-transform: uppercase; line-height: 1.05; white-space: nowrap; }
  .net { font-family: "Oswald", sans-serif; font-weight: 500; font-size: 20px; color: var(--white); }

  /* back */
  .serving { left: 28px; top: 148px; width: 270px; height: 150px; border-radius: 60px; background: linear-gradient(135deg, var(--green-deep), var(--green-bright)); color: var(--white); padding: 20px 22px; }
  .serving h3 { font-family: "Oswald", sans-serif; font-weight: 500; font-size: 17px; margin-bottom: 4px; }
  .serving p { font-size: 11px; line-height: 15px; }
  .ingredients { left: 110px; top: 312px; width: 240px; }
  .ingredients h3 { font-family: "Oswald", sans-serif; font-weight: 500; font-size: 14px; color: var(--ink); margin-bottom: 3px; }
  .ingredients p { font-size: 10px; line-height: 13px; color: var(--grey); }
  .nutrition { left: 56px; top: 414px; width: 272px; font-size: 9.5px; color: var(--grey); }
  .nutrition-head { background: var(--green); color: var(--white); font-family: "Oswald", sans-serif; font-size: 10px; padding: 3px 6px; width: 190px; }
  .nutrition-meta { display: flex; justify-content: space-between; background: #e8f3df; padding: 3px 6px; }
  .nutrition table { width: 100%; border-collapse: collapse; background: var(--white); }
  .nutrition th { font-weight: 400; padding: 2px 4px; text-align: center; line-height: 11px; }
  .nutrition td { padding: 1.5px 4px; border-bottom: 1px solid #d6d6d6; text-align: center; }
  .nutrition td:first-child { text-align: left; }
  .energy-pill { left: 338px; top: 420px; width: 152px; height: 96px; border-radius: 48px; background: linear-gradient(135deg, var(--lime), var(--green) 70%); padding: 15px 14px 0 18px; font-family: "Oswald", sans-serif; line-height: 1; white-space: nowrap; }
  .energy-pill .dark { color: var(--ink); font-size: 11px; font-weight: 500; }
  .energy-pill .light { color: var(--white); font-size: 17px; font-weight: 500; margin-top: 4px; }
  .energy-pill .light small { display: block; font-size: 12px; }
  .maker { left: 232px; top: 596px; width: 140px; height: 140px; border-radius: 50%; background: linear-gradient(135deg, var(--green-deep), var(--green-bright)); color: var(--white); text-align: center; padding-top: 26px; font-size: 7.5px; line-height: 10.5px; }
  .maker strong { display: block; font-weight: 400; font-size: 9.5px; margin-bottom: 10px; }
  .social { left: 30px; top: 616px; font-size: 10px; color: var(--grey); }
  .social-dots { display: flex; gap: 5px; margin-top: 6px; }
  .social-dots i { width: 13px; height: 13px; border-radius: 50%; background: #8a9aa8; }
  .contact { left: 30px; top: 684px; font-size: 11px; color: var(--ink); }
</style>
</head>
<body>

<section class="pouch pouch--front" aria-label="Front of pouch">
  <div class="leaf-band" role="img" aria-label="Pattern of light green tea leaves on a green band"></div>

  <div class="abs hero-frame">
    <div class="abs hero">
      <div class="abs hero-photo" role="img" aria-label="Photograph of fresh turmeric root, ginger and a bowl of turmeric powder"></div>
      <svg class="abs hero-curve" width="456" height="280" viewBox="0 0 456 280" aria-hidden="true">
        <path d="M0 0 H300 C210 70 190 190 280 280 H0 Z" fill="#fdfcf6"/>
      </svg>
      <div class="abs brand-art" style="left:50px;top:30px" role="img" aria-label="Brand illustration of a woman in profile with flowing leaves"></div>
      <div class="abs brand-name" style="left:36px;top:124px;font-size:48px">Vontrisa</div>
      <div class="abs kicker" style="left:40px;top:196px">TURMERIC <span>THAI TEA</span></div>
      <p class="abs tagline" style="left:40px;top:214px">The flavor sensation that energizes<br>your bodies Cells<br>giving them all the food<br>it needs to be healthy</p>
      <div class="abs title-serif" style="left:296px;top:60px">Turmeric<br>THAI</div>
      <div class="abs title-tea" style="left:298px;top:118px">TEA</div>
      <div class="abs title-sub" style="left:282px;top:236px">- TASTE SENSATION -</div>
    </div>
  </div>
  <div class="abs seam"></div>

  <div class="abs ingredient ing-turmeric" style="left:38px;top:424px" role="img" aria-label="Turmeric root"></div>
  <div class="abs ingredient ing-cinnamon" style="left:128px;top:424px" role="img" aria-label="Cinnamon sticks and powder"></div>
  <div class="abs ingredient ing-pepper" style="left:218px;top:424px" role="img" aria-label="Black peppercorns"></div>
  <div class="abs ingredient ing-fennel" style="left:308px;top:424px" role="img" aria-label="Fennel seeds"></div>
  <div class="abs ingredient ing-kelp" style="left:398px;top:416px" role="img" aria-label="Kelp underwater"></div>
  <div class="abs ingredient ing-seaweed" style="left:128px;top:502px" role="img" aria-label="Seaweed"></div>
  <div class="abs ingredient ing-stevia" style="left:218px;top:498px" role="img" aria-label="Stevia leaves"></div>
  <div class="abs ingredient ing-vanilla" style="left:308px;top:492px" role="img" aria-label="Vanilla flower and pods"></div>

  <div class="abs claim-box">
    <div class="abs claim-frame">
      <div class="claim" style="padding:8px 0 0 8px">
        <div style="font-size:24px">Delicious</div>
        <div style="font-size:36px">Spices</div>
        <div style="font-size:20px">And Unique</div>
        <div style="font-size:32px">Powder</div>
      </div>
    </div>
  </div>

  <div class="abs origin-mark" aria-hidden="true"></div>
  <div class="abs origin">AUSTRALIAN<small>MADE &amp; OWNED</small></div>

  <div class="abs mini-block">
    <div class="brand-art" style="width:80px;height:36px;margin-left:50px" role="img" aria-label="Small brand illustration of a woman in profile with leaves"></div>
    <div class="brand-name" style="font-size:30px;margin-top:2px">Vontrisa</div>
    <div class="mini-sub"><span>TURMERIC</span> THAI TEA</div>
    <div class="mini-list">Cinnamon, Turmeric, Fennel, Stevia and Vanilla<br>Black Pepper, Kelp, Seaweed</div>
    <div class="method" style="margin-top:6px"><span style="font-size:10px">The</span> <span style="font-size:18px;font-weight:500">Marlow Fenwick</span></div>
    <div class="method" style="font-size:16px;color:var(--white)">Method <span style="font-size:7.5px;color:var(--gold-soft)">and so much less</span></div>
    <div class="net" style="margin:4px 0 0 78px">342G NET</div>
  </div>
</section>

<section class="pouch pouch--back" aria-label="Back of pouch">
  <div class="leaf-band" role="img" aria-label="Pattern of light green tea leaves on a green band"></div>

  <svg class="abs" style="left:0;top:0" width="500" height="740" viewBox="0 0 500 740" aria-hidden="true">
    <circle cx="250" cy="470" r="190" fill="none" stroke="#3aa84a" stroke-width="34"/>
    <path d="M110 330 A170 170 0 0 1 420 420" fill="none" stroke="#f8cf3a" stroke-width="26" opacity=".8"/>
    <line x1="250" y1="315" x2="338" y2="440" stroke="#3aa84a" stroke-width="1.5"/>
    <line x1="400" y1="520" x2="340" y2="610" stroke="#3aa84a" stroke-width="1.5"/>
  </svg>

  <div class="abs serving">
    <h3>Serving Suggestion:</h3>
    <p>Prepare Vontrisa as you would your regular tea – just add to hot water, and let infuse for 1 – 2 minutes. The screw cap bottle included in the pouch is the recommended serve.</p>
  </div>

  <div class="abs brand-art" style="left:318px;top:148px;width:160px;height:76px" role="img" aria-label="Brand illustration of a woman in profile with flowing leaves"></div>
  <div class="abs brand-name" style="left:310px;top:226px;font-size:50px">Vontrisa</div>

  <div class="abs ingredients">
    <h3>Ingredients</h3>
    <p>Turmeric, Cinnamon, Ground fennel, Vanilla, Calcium Carbonate (E170), Sodium bicarbonate (E500), Ascorbic Acid (E300), Kelp (0.16g), Black Pepper, Stevia, Green Tea, Aniseed, Caraway, Ginger, Liquarice, Cloves, Cardomom</p>
  </div>

  <div class="abs nutrition">
    <div class="nutrition-head">NUTRITIONAL INFORMATION</div>
    <div class="nutrition-meta"><span>Servings per package: 31.00</span><span>Serving size: 10.90g</span></div>
    <table>
      <tr><th></th><th>Average Quantity<br>per Serving</th><th>Average Quantity<br>per 100g</th></tr>
      <tr><td>Energy</td><td>126 kj</td><td>1060kj</td></tr>
      <tr><td>Protein</td><td>0.6g</td><td>5.4g</td></tr>
      <tr><td>Fat total</td><td>0.9g</td><td>8.1g</td></tr>
      <tr><td>Carbohydrates</td><td>3.6g</td><td>32.8g</td></tr>
      <tr><td>Sugar</td><td>1.9g</td><td>17.6g</td></tr>
      <tr><td>Sodium</td><td>55mg</td><td>509mg</td></tr>
    </table>
  </div>

  <div class="abs energy-pill">
    <div class="dark">VONTRISA BEING<br><span style="font-size:14px">CELLULAR ENERGY</span></div>
    <div class="light">DRINK TURMERIC<small>TASTE SENSATION</small></div>
  </div>

  <div class="abs maker">
    Manufactured in Australia for
    <strong>Brightleaf Holdings LLC</strong>
    Product returns<br>Suite 210, Brightleaf Holdings LLC<br>4120 Harbor View Rd<br>Coral Bay FL 33000
  </div>

  <div class="abs social">follow us on<div class="social-dots" aria-hidden="true"><i></i><i></i><i></i></div></div>
  <div class="abs contact">info@vontrisa.com &nbsp;|&nbsp; www.vontrisa.com</div>
</section>

</body>
</html>
```